Healthy lifestyle Influencer business card

I need your creativity to have a business card that I can leave in all the restaurants, hotels and spas I visit to inform them that I am an influencer specializing in the wellness sector and that I will write a review about them. You can use my instagram photos Lunavita27 or on my website www.piattileggeriorto.it. I would like my business card to impress with its creativity! thank you very much!

Contact Information for Business Card

siteweb, instagram, phone number

Font styles to use
Decorative
Script

Colors
0094D4
00A9DD
6FCCEA
C7EBF8
E9F6FB
59FF00
82FF00
B8FF75
E3FFCB
F4FFEA
FFC000
F8CF3A
FAE287
FDF2CF
FEFAEE
F0912C
F2A743
F7CA91
FBE8D2
FDF5EE
EE7325
F08F49
F5BC92
FAE3D3
FDF4ED
EB3D1F
EC4F4E
F09395
F8D3D4
FCEDEE
E54698
E96AAD
F1A4CE
F9D9EA
FCEFF6

Requirements
Nice to have
• creativity

```html
<!DOCTYPE html>
<html lang="it">
<head>
<meta charset="utf-8">
<title>Luna Vita Chef – biglietto da visita</title>
<link href="https://fonts.googleapis.com/css2?family=Great+Vibes&family=Roboto:wght@400&display=swap" rel="stylesheet">
<style>
  :root {
    --backdrop: #2f2f2f;
    --card: #222324;
    --card-edge: #2b2c2d;
    --ink-deep: #121212;
    --ink-light: #f2f2f2;
    --ink-muted: #cfd0d0;
    --accent: #9fc2b9;
  }
  * { margin: 0; padding: 0; box-sizing: border-box; }
  html, body { width: 1200px; height: 1138px; overflow: hidden; background: var(--backdrop); }
  .canvas { position: relative; width: 1200px; height: 1138px; }
  .card {
    position: absolute;
    width: 620px;
    height: 376px;
    border-radius: 16px;
    background: linear-gradient(160deg, var(--card) 0%, var(--card-edge) 100%);
    overflow: hidden;
  }
  .card-front { left: 272px; top: 184px; }
  .card-back { left: 274px; top: 606px; }

  .brand-name {
    font-family: "Great Vibes", cursive;
    font-weight: 400;
    white-space: nowrap;
  }
  .card-front .brand-name {
    position: absolute; left: 0; right: 0; top: 140px;
    text-align: center; font-size: 64px; color: var(--ink-deep);
  }
  .handle {
    font-family: "Roboto", sans-serif;
    font-size: 16px;
    color: var(--ink-muted);
    white-space: nowrap;
  }
  .card-front .handle {
    position: absolute; left: 0; right: 0; top: 332px; text-align: center;
  }

  .card-back .accent-ring { position: absolute; left: 340px; top: 40px; }
  .card-back .brand-name {
    position: absolute; left: 36px; top: 66px;
    font-size: 44px; color: var(--ink-light);
  }
  .person-name {
    position: absolute; left: 24px; top: 212px;
    font-family: "Great Vibes", cursive;
    font-size: 38px; color: var(--ink-light); white-space: nowrap;
  }
  .contact-list { position: absolute; left: 34px; top: 268px; list-style: none; }
  .contact-list li {
    display: flex; align-items: center; gap: 14px; height: 24px;
    font-family: "Roboto", sans-serif; font-size: 16px; color: var(--ink-muted);
  }
  .contact-list svg { width: 14px; height: 14px; fill: none; stroke: var(--ink-muted); stroke-width: 1.6; }
  .card-back .handle { position: absolute; left: 476px; top: 315px; }
</style>
</head>
<body>
<div class="canvas">
  <section class="card card-front">
    <p class="brand-name">Luna Vita Chef</p>
    <p class="handle">@Lunavita27</p>
  </section>

  <section class="card card-back">
    <svg class="accent-ring" width="280" height="280" viewBox="0 0 280 280" aria-hidden="true">
      <circle cx="140" cy="140" r="128" fill="none" stroke="var(--accent)" stroke-width="4"/>
    </svg>
    <p class="brand-name">Luna Vita Chef</p>
    <p class="person-name">Luna Ferraro</p>
    <ul class="contact-list">
      <li>
        <svg viewBox="0 0 16 16" aria-hidden="true"><path d="M4 2l3 3-2 2c1 2 2 3 4 4l2-2 3 3-2 2C7 14 2 9 2 4z"/></svg>
        000-0000-0000
      </li>
      <li>
        <svg viewBox="0 0 16 16" aria-hidden="true"><rect x="1.5" y="3.5" width="13" height="9"/><path d="M1.5 3.5l6.5 5 6.5-5"/></svg>
        info@piattileggeriorto.it
      </li>
      <li>
        <svg viewBox="0 0 16 16" aria-hidden="true"><circle cx="8" cy="8" r="6.5"/><ellipse cx="8" cy="8" rx="3" ry="6.5"/><path d="M1.5 8h13"/></svg>
        www.piattileggeriorto.it
      </li>
    </ul>
    <p class="handle">@Lunavita27</p>
  </section>
</div>
</body>
</html>
```